Business Card Design

Hi I need a business card designed, we already have the business name logo artwork and would like some concept ideas for the Bus Card layout.
On the back of the card i want to include the products and services that we offer.
We are a Plastics Sheeting manufacture based in Perth Australia.

                                       

We need a BC design for a company called Tarvo Plastics based in Perth Australia.

We supply from DIY to Trade & Industrial  Engineering Markets.

We specialise in:

·         Cut to size panels  (all shapes and sizes)

·         Plastics fabrication & Welding

·         Custom Designs

·         Plastic Repairs

·         PVC Pipe Slotting & PVC Pipe Threading

·         Supplier of all types of engineering plastics and profiles.

Including:           Acrylic / Clarvene

                               Polycarbonate / Dorvil

                               Prismatic Light Diffuser

                               Vantrib

                               HDPE / UHMWPE

                               PVC / PVC Foam

                               Nylon

                               HIPS

```html
<!DOCTYPE html>
<html lang="en">
<head>
<meta charset="utf-8">
<title>Tarvo Plastics – Business Card</title>
<link rel="stylesheet" href="https://fonts.googleapis.com/css2?family=Source+Sans+3:ital,wght@0,400;0,600;0,700;1,700&display=swap">
<style>
  :root {
    --navy: #1b2a5a;
    --blue: #2384c0;
    --orange: #e8792b;
    --gold: #f5a623;
    --ink: #3d3d3d;
    --white: #ffffff;
    --backdrop: #e8e9ed;
  }
  * { box-sizing: border-box; margin: 0; padding: 0; }
  html, body { width: 1200px; height: 987px; overflow: hidden; }
  body {
    background: var(--backdrop);
    font-family: "Source Sans 3", Arial, sans-serif;
    display: flex;
    flex-direction: column;
    align-items: center;
    justify-content: center;
    gap: 40px;
  }
  .card {
    position: relative;
    width: 700px;
    height: 428px;
    border-radius: 26px;
    overflow: hidden;
    box-shadow: 0 6px 18px rgba(0,0,0,.15);
  }

  /* Front */
  .card-front { background: var(--white); }
  .name-tab {
    position: absolute; left: 0; top: 30px;
    width: 16px; height: 62px; background: var(--navy);
  }
  .person { position: absolute; left: 40px; top: 34px; }
  .person-name { color: var(--navy); font-weight: 700; font-size: 26px; line-height: 1.1; }
  .person-title { color: var(--orange); font-size: 17px; }
  .contact {
    position: absolute; left: 40px; top: 112px;
    color: var(--ink); font-size: 18px; line-height: 25px;
    list-style: none;
  }
  .contact li { display: flex; align-items: center; gap: 6px; }
  .contact svg { width: 15px; height: 15px; fill: var(--orange); flex: none; }
  .contact .gap { margin-left: 10px; }
  .brand-front {
    position: absolute; left: 330px; top: 176px;
    display: flex; align-items: center; gap: 12px;
    color: var(--navy); font-weight: 700; font-size: 50px; letter-spacing: .5px;
  }
  .brand-mark { width: 22px; height: 22px; background: var(--orange); }
  .footer-band { position: absolute; left: 0; bottom: 0; width: 700px; height: 110px; }
  .legal {
    position: absolute; left: 34px; bottom: 60px;
    color: var(--white); font-size: 16px;
  }

  /* Back */
  .card-back { background: var(--navy); color: var(--white); }
  .brand-back {
    position: absolute; right: 40px; top: 26px;
    font-weight: 700; font-size: 54px; letter-spacing: .5px;
  }
  .tagline {
    position: absolute; left: 30px; right: 30px; top: 100px;
    text-align: center; font-style: italic; font-weight: 700; font-size: 19px; line-height: 1.2;
  }
  .offer-col { position: absolute; top: 160px; }
  .offer-col.services { left: 34px; width: 330px; }
  .offer-col.materials { left: 400px; width: 280px; }
  .offer-heading { color: var(--gold); font-weight: 700; font-size: 24px; margin-bottom: 4px; }
  .offer-list { list-style: none; font-size: 16.5px; line-height: 22px; }
  .offer-list li { position: relative; padding-left: 14px; }
  .offer-list li::before {
    content: ""; position: absolute; left: 0; top: 8px;
    width: 7px; height: 7px; border-radius: 50%; background: var(--gold);
  }
  .offer-list .pair::after { content: none; }
  .inline-dot {
    display: inline-block; width: 7px; height: 7px; border-radius: 50%;
    background: var(--gold); margin: 0 6px 2px 10px;
  }
  .divider {
    position: absolute; left: 375px; top: 170px;
    width: 1px; height: 200px; background: rgba(255,255,255,.5);
  }
</style>
</head>
<body>

  <section class="card card-front">
    <div class="name-tab"></div>
    <div class="person">
      <div class="person-name">Your Name</div>
      <div class="person-title">Title</div>
    </div>
    <ul class="contact">
      <li>Unit 4/18 Kestrel Circuit</li>
      <li>Brookdale WA 6155</li>
      <li>PO Box 2480</li>
      <li>Brookdale DC WA 6970</li>
      <li>
        <svg viewBox="0 0 16 16"><circle cx="8" cy="8" r="7.5"/><path d="M5 4l2 2-1 1.2a6 6 0 0 0 2.8 2.8L10 9l2 2-1.2 1.3C7 12 4 9 3.7 5.2z" fill="#fff"/></svg>
        08 9471 3350
      </li>
      <li>
        <svg viewBox="0 0 16 16"><rect x="4" y="1" width="8" height="14" rx="1.5"/><rect x="5.5" y="3" width="5" height="7" fill="#fff"/></svg>
        123-456-7890
        <svg class="gap" viewBox="0 0 16 16"><rect x="1" y="6" width="14" height="8" rx="1"/><rect x="4" y="2" width="8" height="5"/><rect x="4" y="9" width="8" height="2" fill="#fff"/></svg>
        08 9471 3351
      </li>
      <li>
        <svg viewBox="0 0 16 16"><rect x="1" y="3" width="14" height="10" rx="1.5"/><path d="M2 4l6 5 6-5" stroke="#fff" stroke-width="1.4" fill="none"/></svg>
        sales@tarvoplastics.com.au
      </li>
    </ul>

    <div class="brand-front"><span class="brand-mark"></span>Tarvo Plastics</div>

    <svg class="footer-band" viewBox="0 0 700 110" preserveAspectRatio="none" aria-hidden="true">
      <path d="M0 10 H420 C450 10 460 30 480 55 L700 110 H0 Z" fill="var(--navy)"/>
      <path d="M0 62 H400 C470 62 560 85 640 110 H0 Z" fill="var(--blue)"/>
    </svg>
    <div class="legal">Kestrel Holdings Pty Ltd T/A Tarvo Plastics ABN: TBA</div>
  </section>

  <section class="card card-back">
    <div class="brand-back">Tarvo Plastics</div>
    <p class="tagline">The Products And Services That We Offer<br>Are Supplied From Diy To Trade &amp; Industrial Engineering Markets</p>

    <div class="offer-col services">
      <h2 class="offer-heading">We specialise in:</h2>
      <ul class="offer-list">
        <li>Cut to size panels (all shapes and sizes)</li>
        <li>Plastics fabrication &amp; Welding</li>
        <li>Custom Designs</li>
        <li>Plastic Repairs</li>
        <li>PVC Pipe Slotting &amp; PVC Pipe Threading</li>
        <li>Supplier of all types of engineering plastics and profiles</li>
      </ul>
    </div>

    <div class="divider"></div>

    <div class="offer-col materials">
      <h2 class="offer-heading">Including:</h2>
      <ul class="offer-list">
        <li>Acrylic / Clarvene</li>
        <li>Polycarbonate / Dorvil</li>
        <li>Prismatic Light Diffuser</li>
        <li>Vantrib<span class="inline-dot"></span>HDPE / UHMWPE</li>
        <li>PVC / PVC Foam</li>
        <li>Nylon<span class="inline-dot"></span>HIPS</li>
      </ul>
    </div>
  </section>

</body>
</html>
```